Stationery Design Project

Hi All,

We need you to design stationary for a new Business and Accounting Advisory Firm. We have already got the logo designed and it is attached. If you could also if possible, match the fonts in your design to that on the logo’s provided.

What we need:
- Business Card
- A4 Letter head
- A4 Folders
- PPT template (Title page and regular page)

And what ever else you want to throw in.

We are in the process of getting the web site designed, however below is a list of websites which we like which will give you an understanding of the style that we are going for.

- plivant.example
- moldrabay.example
- tarvenhook.example
- quillorbank.example

I look forward to your seeing your design.
Updates

Hi All,

I have just realised that I forgot that i need to include a Sworn Ledgerkeepers image on the letter head, please find attaced as File 1. Could you please have this image in the bottom left header.

Regards,

Marcus

Industry/Entity Type

Business

Requirements
Must have
• Outputs:
- Documents ready to print
- Generic editable information
- Pdf copies of the documents
- Word version of letterhead

```html
<!DOCTYPE html>
<html lang="en">
<head>
<meta charset="utf-8">
<title>Corrindale Partners – Business Cards</title>
<link rel="stylesheet" href="https://fonts.googleapis.com/css2?family=EB+Garamond:wght@500&family=Tinos:wght@400;700&family=Open+Sans:wght@400&display=swap">
<style>
  :root {
    --board: #898a8c;
    --paper: #ffffff;
    --navy: #3a5b9b;
    --ink: #1e1e1e;
    --ink-soft: #333333;
    --rule: #9a9a9a;
    --orange-deep: #f37a20;
    --orange-glow: #fdd033;
    --blue-deep: #365b9b;
    --blue-glow: #3ec3e3;
    --mark-orange: #f7931e;
  }
  * { margin: 0; padding: 0; box-sizing: border-box; }
  html, body { width: 1200px; height: 709px; overflow: hidden; }
  body { background: var(--board); position: relative; font-family: "Tinos", "Times New Roman", serif; }

  .card { position: absolute; width: 558px; height: 320px; border: 1px solid #4a4a4a; overflow: hidden; }
  .card--front { left: 25px; top: 25px; background: var(--paper); }
  .card--orange { left: 618px; top: 25px; background: radial-gradient(circle at 50% 50%, var(--orange-glow) 0%, #f9a92a 30%, var(--orange-deep) 75%); }
  .card--blue { left: 25px; top: 363px; background: radial-gradient(circle at 53% 50%, var(--blue-glow) 0%, #3a8cc6 30%, var(--blue-deep) 70%); }
  .card--plain { left: 618px; top: 363px; background: var(--paper); }

  .brand { position: absolute; display: flex; align-items: center; gap: 12px; }
  .brand__dot { width: 46px; height: 46px; border-radius: 50%; background: var(--mark-orange); flex: none; }
  .brand__name { font-family: "EB Garamond", Georgia, serif; font-weight: 500; font-size: 31px; line-height: 1; color: var(--navy); white-space: nowrap; }
  .brand__tag { font-family: "Open Sans", Arial, sans-serif; font-size: 12.5px; letter-spacing: 4.6px; color: var(--navy); margin-top: 6px; white-space: nowrap; }

  .card--front .brand { left: 112px; top: 58px; }
  .card--plain .brand { left: 88px; top: 118px; }

  .person { position: absolute; right: 301px; top: 170px; text-align: right; color: var(--ink-soft); font-size: 16.5px; line-height: 1.3; }
  .person__name { font-weight: 700; font-size: 21px; color: var(--navy); line-height: 1.15; }
  .person__role { margin-bottom: 8px; }
  .divider { position: absolute; left: 274px; top: 166px; width: 1px; height: 108px; background: var(--rule); }
  .contact { position: absolute; left: 288px; top: 175px; list-style: none; font-size: 16.5px; color: var(--ink); }
  .contact li { display: flex; align-items: center; gap: 5px; height: 23.5px; }
  .contact svg { width: 12px; height: 12px; fill: var(--navy); flex: none; }

  .wordmark { position: absolute; left: 0; right: 0; text-align: center; font-family: "EB Garamond", Georgia, serif; font-weight: 500; color: var(--paper); font-size: 50px; line-height: 1; }
  .card--orange .wordmark { top: 118px; }
  .card--blue .wordmark { top: 120px; }

  .web { position: absolute; left: 0; right: 0; text-align: center; font-size: 17.5px; letter-spacing: 2px; }
  .card--orange .web, .card--blue .web { color: var(--paper); }
  .card--orange .web { top: 266px; }
  .card--blue .web { top: 266px; }
  .card--plain .web { top: 240px; color: var(--ink); }
</style>
</head>
<body>

  <section class="card card--front">
    <div class="brand">
      <span class="brand__dot"></span>
      <div>
        <div class="brand__name">Corrindale Partners</div>
        <div class="brand__tag">Business Advisors</div>
      </div>
    </div>

    <div class="person">
      <div class="person__name">Your Name</div>
      <div class="person__role">Designation</div>
      <div>Street Name, City Name</div>
      <div>State, City Zip Code</div>
    </div>
    <div class="divider"></div>
    <ul class="contact">
      <li><svg viewBox="0 0 12 12"><path d="M3 1l2 2.5-1.2 1.3c.6 1.4 1.7 2.6 3.2 3.2L8.3 6.8 11 9l-1.3 2C5 10.5 1.3 6.8 1 2.3z"/></svg>0123-456-789</li>
      <li><svg viewBox="0 0 12 12"><path d="M3.5 0h5A1 1 0 0 1 9.5 1v10a1 1 0 0 1-1 1h-5a1 1 0 0 1-1-1V1a1 1 0 0 1 1-1zM3.5 1.5v7.5h5V1.5z"/></svg>0123-456-789</li>
      <li><svg viewBox="0 0 12 12"><path d="M0 2h12v8H0zM1 3v.4l5 3.4 5-3.4V3z"/></svg>info@corrindalepartners.example</li>
      <li><svg viewBox="0 0 12 12"><path d="M6 0a6 6 0 1 0 0 12A6 6 0 0 0 6 0zm0 1.2c.8.8 1.3 2.1 1.4 3.9H4.6C4.7 3.3 5.2 2 6 1.2zM1.3 6.8h2.2c.1 1.6.5 2.9 1.1 3.8a4.8 4.8 0 0 1-3.3-3.8zm3.3 0h2.8C7.3 8.6 6.8 9.9 6 10.8 5.2 9.9 4.7 8.6 4.6 6.8zm3.9 0h2.2a4.8 4.8 0 0 1-3.3 3.8c.6-.9 1-2.2 1.1-3.8zm0-1.7c-.1-1.6-.5-2.9-1.1-3.8a4.8 4.8 0 0 1 3.3 3.8zm-5 0H1.3a4.8 4.8 0 0 1 3.3-3.8c-.6.9-1 2.2-1.1 3.8z"/></svg>www.corrindalepartners.example</li>
    </ul>
  </section>

  <section class="card card--orange">
    <div class="wordmark">Corrindale Partners</div>
    <div class="web">www.corrindalepartners.example</div>
  </section>

  <section class="card card--blue">
    <div class="wordmark">Corrindale Partners</div>
    <div class="web">www.corrindalepartners.example</div>
  </section>

  <section class="card card--plain">
    <div class="brand">
      <span class="brand__dot"></span>
      <div>
        <div class="brand__name">Corrindale Partners</div>
        <div class="brand__tag">Business Advisors</div>
      </div>
    </div>
    <div class="web">www.corrindalepartners.example</div>
  </section>

</body>
</html>
```